PHD-project

i need the figures to be in the same stile. info is inside the file. There are 5 figures that need redesign. this is for PhD.

Target Market(s)

it will be used in my phd

Colors

```html
<!DOCTYPE html>
<html lang="en">
<head>
<meta charset="utf-8">
<title>Contribution Area — Venn Diagram</title>
<link rel="stylesheet" href="https://fonts.googleapis.com/css2?family=Sora:wght@500&display=swap">
<style>
  :root {
    --canvas-bg: #ffffff;
    --label-colour: #ffffff;
    --blue-light: #7be9fc;
    --blue-mid: #3ab2ee;
    --blue-deep: #2157bd;
    --teal-light: #a3e2dd;
    --teal-mid: #4db5b3;
    --teal-deep: #05847f;
    --teal-glow: #14e3e6;
    --overlap-light: #0893cc;
    --overlap-mid: #0d5a98;
    --overlap-deep: #012f60;
  }
  html, body {
    margin: 0;
    padding: 0;
    overflow: hidden;
    background: var(--canvas-bg);
  }
  .canvas {
    width: 1200px;
    height: 780px;
    position: relative;
    background: var(--canvas-bg);
  }
  .venn {
    display: block;
    width: 1200px;
    height: 780px;
  }
  .venn-label {
    font-family: "Sora", sans-serif;
    font-weight: 500;
    font-size: 24px;
    fill: var(--label-colour);
    text-anchor: middle;
    filter: drop-shadow(0 1px 2px rgba(0, 30, 60, 0.25));
  }
</style>
</head>
<body>
<main class="canvas">
  <svg class="venn" viewBox="0 0 1200 780" xmlns="http://www.w3.org/2000/svg" role="img"
       aria-label="Venn diagram: Design Thinking in Management and Business Strategy overlaps Research Through Design in the Contribution Area">
    <defs>
      <radialGradient id="management-fill" cx="432" cy="240" r="330" gradientUnits="userSpaceOnUse">
        <stop offset="0" stop-color="var(--blue-light)"/>
        <stop offset="0.5" stop-color="var(--blue-mid)"/>
        <stop offset="1" stop-color="var(--blue-deep)"/>
      </radialGradient>
      <radialGradient id="research-fill" cx="690" cy="258" r="360" gradientUnits="userSpaceOnUse">
        <stop offset="0" stop-color="var(--teal-light)"/>
        <stop offset="0.5" stop-color="var(--teal-mid)"/>
        <stop offset="1" stop-color="var(--teal-deep)"/>
      </radialGradient>
      <linearGradient id="research-rim" x1="0" y1="0" x2="0" y2="1">
        <stop offset="0" stop-color="var(--teal-glow)" stop-opacity="0.8"/>
        <stop offset="0.25" stop-color="var(--teal-glow)" stop-opacity="0"/>
      </linearGradient>
      <linearGradient id="overlap-fill" x1="0.2" y1="0.15" x2="0.55" y2="1">
        <stop offset="0" stop-color="var(--overlap-light)"/>
        <stop offset="0.5" stop-color="var(--overlap-mid)"/>
        <stop offset="1" stop-color="var(--overlap-deep)"/>
      </linearGradient>
      <clipPath id="management-clip">
        <circle cx="474" cy="390" r="225"/>
      </clipPath>
    </defs>

    <g class="set set--management">
      <circle cx="474" cy="390" r="225" fill="url(#management-fill)"/>
    </g>
    <g class="set set--research">
      <circle cx="747" cy="390" r="225" fill="url(#research-fill)"/>
      <circle cx="747" cy="390" r="225" fill="url(#research-rim)"/>
    </g>
    <g class="set set--overlap" clip-path="url(#management-clip)">
      <circle cx="747" cy="390" r="225" fill="url(#overlap-fill)"/>
    </g>

    <text class="venn-label" x="388" y="344">
      <tspan x="388">Design Thinking</tspan>
      <tspan x="388" dy="35">in Management</tspan>
      <tspan x="388" dy="35">&amp; Business</tspan>
      <tspan x="388" dy="35">Strategy</tspan>
    </text>
    <text class="venn-label" x="611" y="379">
      <tspan x="611">Contribution</tspan>
      <tspan x="611" dy="35">Area</tspan>
    </text>
    <text class="venn-label" x="829" y="361">
      <tspan x="829">Research</tspan>
      <tspan x="829" dy="35">Through Design</tspan>
      <tspan x="829" dy="35">-RTD</tspan>
    </text>
  </svg>
</main>
</body>
</html>
```